Local Roofing/Construction company business needs new biz card design

We need a new business card design, current cards are from the start of this operation and generic at best. We are a local Construction Company (General Contractor) with a majority of our work originating from insurance claims-exterior finish work is the main focus (Roofs-Siding-Gutters etc). Heavily involved with homeowners and the low ball offers they receive from insurance company's after a insurable event takes place. I have attached some of our original logo file(s) below.

```html
<!DOCTYPE html>
<html lang="en">
<head>
<meta charset="utf-8">
<title>Ridgeline Build – Business Card</title>
<link rel="stylesheet" href="https://fonts.googleapis.com/css2?family=Montserrat:wght@400;500;700&display=swap">
<style>
  :root {
    --backdrop: #3b3532;
    --card-dark: #101a1b;
    --card-mid: #1c2a2b;
    --brand-green: #4fae5f;
    --edge-green: #2fa03c;
    --text-light: #e4e9e8;
    --rule-green: #3f8f4d;
  }
  * { box-sizing: border-box; margin: 0; padding: 0; }
  html, body { width: 1200px; height: 716px; overflow: hidden; }
  body {
    background: var(--backdrop);
    font-family: "Montserrat", sans-serif;
    position: relative;
  }
  .card {
    position: absolute;
    top: 210px;
    width: 520px;
    height: 297px;
    border-radius: 3px;
    overflow: hidden;
    box-shadow: 0 14px 30px rgba(0,0,0,0.45);
  }
  /* pattern side */
  .card--back { left: 45px; border-bottom: 5px solid var(--edge-green); }
  .card--back .pattern-field {
    position: absolute; inset: 0;
    background: linear-gradient(120deg, #121c1d 0%, #17262a 55%, #223538 100%);
  }
  .card--back .back-mark {
    position: absolute;
    right: 150px; bottom: 52px;
    display: flex; align-items: center; gap: 6px;
  }
  .back-mark .mark-square {
    width: 14px; height: 14px; background: var(--brand-green); border-radius: 2px;
  }
  .back-mark .mark-name {
    font-size: 10px; font-weight: 700; color: var(--brand-green);
    letter-spacing: 0.5px; text-transform: uppercase;
  }
  /* contact side */
  .card--front {
    left: 635px;
    background: linear-gradient(135deg, var(--card-mid) 0%, var(--card-dark) 60%, #0c1415 100%);
  }
  .brand {
    position: absolute;
    left: 28px; top: 118px;
    display: flex; align-items: center; gap: 10px;
  }
  .brand .brand-square {
    width: 34px; height: 34px; background: var(--brand-green); border-radius: 3px;
  }
  .brand .brand-name {
    font-size: 21px; font-weight: 700; color: var(--brand-green);
    text-transform: uppercase; letter-spacing: 0.5px; line-height: 1.05;
  }
  .divider {
    position: absolute; left: 268px; top: 70px;
    width: 1.5px; height: 150px; background: var(--rule-green);
  }
  .contact {
    position: absolute; left: 288px; top: 76px;
    color: var(--text-light);
  }
  .contact .person-name {
    font-size: 17px; font-weight: 700; color: var(--brand-green);
    letter-spacing: 1.5px; text-transform: uppercase;
  }
  .contact .person-role {
    font-size: 11px; font-weight: 400; margin-top: 2px; margin-bottom: 12px;
  }
  .contact-list { list-style: none; }
  .contact-list li {
    display: flex; align-items: center; gap: 7px;
    font-size: 11.5px; font-weight: 400; margin-bottom: 5px;
  }
  .contact-list svg { width: 10px; height: 10px; fill: var(--brand-green); flex: none; }
  .contact-list .accent { color: var(--brand-green); }
  .address { margin-top: 8px; font-size: 11.5px; line-height: 1.45; }
</style>
</head>
<body>

<section class="card card--back" aria-label="Card reverse">
  <div class="pattern-field" role="img" aria-label="Faint repeated brand mark pattern on dark teal-black"></div>
  <div class="back-mark">
    <span class="mark-square"></span>
    <span class="mark-name">Ridgeline Build</span>
  </div>
</section>

<section class="card card--front" aria-label="Card front">
  <div class="brand">
    <span class="brand-square"></span>
    <span class="brand-name">Ridgeline<br>Build</span>
  </div>

  <div class="divider"></div>

  <div class="contact">
    <p class="person-name">Marcus Hale</p>
    <p class="person-role">Managing Director</p>
    <ul class="contact-list">
      <li>
        <svg viewBox="0 0 10 10" aria-hidden="true"><path d="M2 0.5 L3.6 0.5 L4.3 2.8 L3.2 3.7 Q4.2 5.8 6.3 6.8 L7.2 5.7 L9.5 6.4 L9.5 8 Q9.5 9.5 8 9.5 Q0.5 9 0.5 2 Q0.5 0.5 2 0.5 Z"/></svg>
        <span>0400 555 127</span>
      </li>
      <li>
        <svg viewBox="0 0 10 10" aria-hidden="true"><path d="M0.5 2 H9.5 V8.5 H0.5 Z M1 2.5 L5 5.6 L9 2.5 V3.4 L5 6.6 L1 3.4 Z" fill-rule="evenodd"/></svg>
        <span>info@ridgelinebuild.com</span>
      </li>
      <li>
        <svg viewBox="0 0 10 10" aria-hidden="true"><circle cx="5" cy="5" r="4.5"/></svg>
        <span>www.<span class="accent">ridgelinebuild</span>.com</span>
      </li>
    </ul>
    <p class="address">418 Mill Creek Road<br>Ashford County Name 5120</p>
  </div>
</section>

</body>
</html>
```